Please design a bold yet creative new "Folder Design" for our new school!

We need a bold folder design to attract new students/families between the ages of 10-14 and to attract new teachers to our school. Our school, Varlo Ridge Eastfield Academy, is one year old and located in Washington, DC. We are looking for a creative design that represents community, our logo/mascot and our commitment to and through college.

Target Market(s)

The target market for this folder is for young parents aged 20-25 and for recent college graduates, aged 22-30.

Industry/Entity Type

School

Colors
0255a3
33a6d7
ffffff

Requirements
Must have
• - Be formatted to the "TwinSleeve" indesign file. - http://pressnook.example/g/showStaticPage.do?page=download_templates-pres.html- Be a presentation folder, 9x12, with two pockets and a right pocket slit.- Be a bold color, consider navy blue for the background (white for contrast writing?)- Have our Varlo Ridge logo present somewhere on the front page.- Have our mascot highlighted somewhere.- Use our Varlo fonts, attached in file section.- Contact information on the inside left pocket should be there:Varlo Ridge Northeast AcademyT: 202-398-5477W: www.kippdc.orgA: 1375 Mount Olivet Road, NEWashington, DC 20099
Nice to have
• - Word art would be nice to have, like at this link: http://www.tanvo-pell.example/wp-content/uploads/2013/03/bookmark.jpg.- A "name box" on the front page could be nice to have. - "Founded in 2014" could be nice to have.- A creative
Should not have
• - It should not be busy.

```html
<!DOCTYPE html>
<html lang="en">
<head>
<meta charset="utf-8">
<title>Varlo Ridge Eastfield Academy – Folder Cover</title>
<link rel="stylesheet" href="https://fonts.googleapis.com/css2?family=Source+Sans+3:wght@300;400;600&display=swap">
<style>
  :root {
    --page-bg: #ececec;
    --cover-gray: #dcdcde;
    --navy: #34578a;
    --slate: #657f9f;
    --mid-blue: #436595;
    --light-blue: #8aa0c0;
    --corner-blue: #4a6ea6;
    --white: #ffffff;
    --photo-reader: #6f6a8f;
    --photo-writer: #b9c3cc;
    --photo-graduate: #8a8a8f;
    --photo-student: #c89a64;
  }
  * { margin: 0; padding: 0; box-sizing: border-box; }
  html, body {
    width: 1200px; height: 802px; overflow: hidden;
    background: var(--page-bg);
    font-family: "Source Sans 3", sans-serif;
  }
  .folder-cover {
    position: absolute; left: 340px; top: 56px;
    width: 520px; height: 690px;
    background: var(--cover-gray);
    box-shadow: 0 6px 18px rgba(0,0,0,.12);
    overflow: hidden;
  }
  .cover-art { position: absolute; inset: 0; width: 520px; height: 690px; }
  .brand {
    position: absolute; left: 250px; top: 96px;
    color: var(--white);
  }
  .brand-name {
    display: flex; align-items: center; gap: 8px;
    font-weight: 600; font-size: 30px; line-height: 1;
  }
  .brand-dot { width: 10px; height: 10px; border-radius: 50%; background: var(--white); }
  .brand-campus { font-weight: 400; font-size: 14px; margin: 4px 0 0 18px; }
  .tagline {
    position: absolute; left: 118px; top: 598px; width: 210px;
    text-align: center; color: var(--white);
    font-weight: 400; font-size: 16px; line-height: 1.4; letter-spacing: .3px;
  }
  .web-address {
    position: absolute; right: 14px; bottom: 14px;
    color: var(--white); font-size: 10px; letter-spacing: .2px;
  }
</style>
</head>
<body>
<main class="folder-cover">
  <svg class="cover-art" viewBox="0 0 520 690" xmlns="http://www.w3.org/2000/svg">
    <defs>
      <linearGradient id="tone-student" x1="0" y1="0" x2="1" y2="1">
        <stop offset="0" stop-color="#d4a24a"/><stop offset=".55" stop-color="#b98a5e"/><stop offset="1" stop-color="#d9c060"/>
      </linearGradient>
      <linearGradient id="tone-graduate" x1="0" y1="0" x2="0" y2="1">
        <stop offset="0" stop-color="#a9abb0"/><stop offset="1" stop-color="#6e7078"/>
      </linearGradient>
    </defs>

    <rect class="photo" role="img" aria-label="Student reading a book" x="40" y="185" width="144" height="130" fill="var(--photo-reader)"/>
    <rect class="photo" role="img" aria-label="Student writing at a classroom desk" x="186" y="185" width="210" height="100" fill="var(--photo-writer)"/>
    <rect class="photo" role="img" aria-label="Smiling graduate in cap and gown" x="40" y="317" width="144" height="373" fill="url(#tone-graduate)"/>
    <rect class="photo" role="img" aria-label="Smiling young student in close-up" x="186" y="287" width="334" height="403" fill="url(#tone-student)"/>

    <polygon class="panel-slate" points="30,0 290,0 168,108" fill="var(--slate)"/>
    <polygon class="panel-navy" points="290,0 400,0 520,65 520,140 390,285 168,108" fill="var(--navy)"/>
    <polygon class="panel-mid" points="520,140 520,430 390,285" fill="var(--mid-blue)"/>
    <polygon class="panel-light" points="60,690 218,478 410,690" fill="var(--light-blue)"/>
    <polygon class="panel-corner" points="440,690 520,690 520,560" fill="var(--corner-blue)"/>

    <g class="divider-lines" stroke="var(--white)" stroke-width="2" fill="none">
      <line x1="520" y1="140" x2="218" y2="478"/>
      <line x1="40" y1="340" x2="218" y2="478"/>
    </g>
  </svg>

  <div class="brand">
    <div class="brand-name"><span class="brand-dot"></span>Varlo Ridge</div>
    <div class="brand-campus">Eastfield Academy</div>
  </div>

  <p class="tagline">learn &nbsp;|&nbsp; lead &nbsp;|&nbsp; innovate<br>Founded in 2014</p>
  <p class="web-address">www.varloridge.example</p>
</main>
</body>
</html>
```